Simple, 1-Page Project - Life-saving AED Devices

We recently kicked off a project to bring all geographic location records for automatic emergency defibrillators (AEDs) in the State of New York online (instead of kept in paper in drawers). This hope is that is will ultimately save thousands of lives, as 9-1-1 operators will be able to quickly direct civilians to the nearest AED to bring to people suffering a cardiac event (e.g., a heart attack).

This page will be used to describe this effort, our progress thus far and how far we have left to go.

I am looking for a 1-page design - coded for both a responsive version for mobile devices and a traditional version - that would ***ideally*** plug into my existing WordPress site (https://qv-lmt.org), but it's not a requirement.

Target Market(s)

General public (non-physicians/non-EMTs)

Requirements
Must have
• - Our logo (please note, our logo is the Birchfield Vale Chapter logo...attached)
Nice to have
• - Would be wonderful to have an area with a clickable map showing where the participating regions are - which, once clicked, will take to you their specific sites. Regions are large chunks of land encompassing multiple towns, NOT a singular, specific place A nice-looking Google Map, a la Plumtail Grids (https://plumtailgrids.com/) would be cool if this were possible..
• - If you need a headline or page title, you can use: "Bringing AEDs in New York Online"
• - Would be nice if the design incorporated the color scheme of our brand (see attachment) and/or our main website: https://qv-lmt.org/
• - Would be nice to have some AED imagery - I attached some common symbols seen in AED advertising for inspiration
Should not have
• - This is a serious topic, so the design should be respectful and not too silly/cartoonish
• - Stock images, if chosen, should be thoughtful and classy

```html
<!DOCTYPE html>
<html lang="en">
<head>
<meta charset="utf-8">
<title>Bringing AEDs in New York Online — Birchfield Vale Chapter</title>
<link href="https://fonts.googleapis.com/css2?family=EB+Garamond:wght@400;500&family=Mulish:wght@400;600&family=Montserrat:wght@700&display=swap" rel="stylesheet">
<style>
:root{
  --navy:#1d2a5a;
  --navy-deep:#1b2856;
  --orange:#d8801a;
  --grey:#e6e6e6;
  --ink:#2b2b2b;
  --white:#ffffff;
  --map:#2b2b2b;
}
*{margin:0;padding:0;box-sizing:border-box}
html,body{width:1200px;height:3401px;overflow:hidden;background:var(--white)}
body{position:relative;font-family:"Mulish",sans-serif;color:var(--ink)}
.abs{position:absolute}
.serif{font-family:"EB Garamond",serif}

/* header */
.site-header{top:0;left:0;width:1200px;height:130px;background:var(--white);z-index:3}
.brand-mark{left:74px;top:16px;width:100px;height:100px;border-radius:50%;border:3px solid var(--navy)}
.brand-rule{left:193px;top:32px;width:2px;height:66px;background:var(--navy)}
.brand-name{left:212px;top:36px;font-family:"EB Garamond",serif;color:var(--navy);font-size:32px;line-height:1.1;width:320px;white-space:nowrap}
.main-nav{top:63px;left:545px;display:flex;align-items:center;gap:30px;font-family:"EB Garamond",serif;font-size:14px;color:var(--ink);letter-spacing:.3px}

/* hero */
.hero{top:122px;left:0;width:1200px;height:549px;background:linear-gradient(120deg,#8a3a3a 0%,#6b2a66 35%,#5b2a5a 60%,#3b2a3c 100%)}
.hero-curve{top:118px;left:0;z-index:2}
.hero-badge{top:252px;left:560px;width:80px;height:92px;background:linear-gradient(180deg,#ffffff 0%,#f4d6d8 100%);border-radius:6px;z-index:2}
.hero-title{top:370px;left:0;width:1200px;text-align:center;color:var(--white);font-size:33px;z-index:2}
.hero-sub{top:423px;left:0;width:1200px;text-align:center;color:var(--white);font-size:17px;z-index:2}
.btn-shop{top:480px;left:521px;width:158px;height:34px;background:var(--navy);color:var(--white);font-family:"Montserrat",sans-serif;font-weight:700;font-size:13px;display:flex;align-items:center;justify-content:center;z-index:2}

/* how it works */
.section-title{font-family:"EB Garamond",serif;color:var(--navy);font-size:43px;text-align:center;font-weight:500}
.step-ring{width:190px;height:190px;border-radius:50%;border:8px solid var(--navy);top:854px}
.step-num{width:48px;height:48px;border-radius:50%;background:var(--orange);color:var(--white);font-family:"EB Garamond",serif;font-size:19px;display:flex;align-items:center;justify-content:center}
.step-title{width:300px;text-align:center;top:1064px;font-family:"EB Garamond",serif;font-size:19px;color:var(--ink)}
.step-text{width:300px;text-align:center;top:1094px;font-size:18px;line-height:22px;color:var(--ink);white-space:nowrap}

/* about / services */
.photo-training{top:1217px;left:0;width:600px;height:500px;background:linear-gradient(135deg,#8c8c8c,#b7b2ad 50%,#6d6a6a)}
.panel-grey{background:var(--grey)}
.copy{font-size:14px;line-height:33px;text-align:center;color:var(--ink);white-space:nowrap}
.photo-sign{top:1717px;left:600px;width:600px;height:490px;background:linear-gradient(90deg,#ededed 0%,#bfbfbf 30%,#1a1fa0 32%,#0b1290 100%)}
.map-area{top:2190px;left:0;width:1200px;height:488px;background:var(--map)}

/* testimonials */
.quote{top:2848px;left:190px;width:820px;text-align:center;font-size:24px;line-height:33px;color:var(--ink)}
.posted{top:2967px;left:0;width:1200px;text-align:center;font-family:"EB Garamond",serif;font-size:15px}
.dot{width:11px;height:11px;border-radius:50%;background:#9a9a9a;top:3030px}

/* footer */
.footer-top{top:3087px;left:0;width:1200px;height:185px;background:var(--navy-deep);color:var(--white)}
.footer-col{position:absolute;top:0;height:185px;text-align:center}
.footer-col h3{font-family:"EB Garamond",serif;font-weight:400;font-size:16px;margin-top:52px;letter-spacing:.4px}
.footer-col p{font-size:10px;line-height:18px;margin-top:16px}
.divider{position:absolute;top:0;width:1px;height:185px;background:#8791b0}
.social{display:flex;gap:33px;justify-content:center;margin-top:30px}
.social span{width:15px;height:15px;border-radius:50%;background:var(--white)}
.email-field{position:absolute;left:790px;top:3184px;width:237px;height:43px;border:1px solid #9aa3c0;color:#aab1c8;font-size:10px;padding:15px 20px}
.btn-submit{position:absolute;left:1035px;top:3184px;width:91px;height:43px;background:var(--orange);color:var(--white);font-size:12px;display:flex;align-items:center;justify-content:center;border:1px solid #f3b36a}
.footer-bottom{top:3272px;left:0;width:1200px;height:129px;background:var(--navy-deep);color:var(--white)}
.footer-nav{position:absolute;top:40px;left:322px;display:flex;align-items:center;gap:30px;font-family:"EB Garamond",serif;font-size:14px}
.copyright{position:absolute;top:77px;width:1200px;text-align:center;font-size:12px}
</style>
</head>
<body>

<header class="abs site-header">
  <div class="abs brand-mark"></div>
  <div class="abs brand-rule"></div>
  <div class="abs brand-name">Birchfield Vale Chapter</div>
  <nav class="abs main-nav">
    <svg width="14" height="13" viewBox="0 0 14 13"><path d="M7 0L0 6h2v7h4V9h2v4h4V6h2z" fill="#2b2b2b"/></svg>
    <span>ABOUT US</span><span>HOW IT WORKS</span><span>SERVICES</span><span>BLOG</span><span>CONTACT US</span>
    <svg width="14" height="14" viewBox="0 0 14 14"><circle cx="5.5" cy="5.5" r="4" fill="none" stroke="#2b2b2b" stroke-width="2"/><path d="M8.5 8.5L13 13" stroke="#2b2b2b" stroke-width="2.4"/></svg>
  </nav>
</header>

<section class="abs hero" role="img" aria-label="Photo of a responder applying AED pads to a patient lying on the floor"></section>
<svg class="abs hero-curve" width="1200" height="50" viewBox="0 0 1200 50"><path d="M0 0H1200V4Q600 10 0 48Z" fill="#fff"/></svg>
<div class="abs hero-badge" role="img" aria-label="AED heart badge illustration"></div>
<h1 class="abs hero-title serif" style="font-weight:400">Bringing AEDs in New York Online</h1>
<p class="abs hero-sub">Sed ut perspiciatis unde omnis iste natus .</p>
<div class="abs btn-shop">SHOP NOW</div>

<h2 class="abs section-title" style="top:738px;left:0;width:1200px">How it Works</h2>

<div class="abs step-ring" style="left:152px"></div>
<div class="abs step-ring" style="left:505px"></div>
<div class="abs step-ring" style="left:865px"></div>
<svg class="abs" style="left:195px;top:905px" width="102" height="75" viewBox="0 0 102 75" fill="none" stroke="#1d2a5a" stroke-width="4"><rect x="3" y="14" width="96" height="58" rx="8"/><rect x="30" y="3" width="42" height="11"/><path d="M42 28h18v10h10v16H60v10H42V54H32V38h10z"/><path d="M3 40h27M72 40h27"/></svg>
<svg class="abs" style="left:553px;top:902px" width="94" height="94" viewBox="0 0 94 94"><path d="M37 4h20v26l22-13 10 18-22 12 22 12-10 18-22-13v26H37V64L15 77 5 59l22-12L5 35l10-18 22 13z" fill="none" stroke="#1d2a5a" stroke-width="5" stroke-linejoin="round"/></svg>
<svg class="abs" style="left:905px;top:902px" width="110" height="96" viewBox="0 0 110 96" fill="#1d2a5a"><path d="M12 2h8v12h12v8H20v12h-8V22H0v-8h12z"/><circle cx="70" cy="14" r="13"/><path d="M44 96V50a20 20 0 0 1 20-20h12a20 20 0 0 1 20 20v46z"/><rect x="6" y="52" width="30" height="40" rx="3" fill="none" stroke="#1d2a5a" stroke-width="4"/><path d="M24 60l-8 13h6l-3 12 9-15h-6z"/></svg>
<div class="abs step-num" style="left:302px;top:879px">01</div>
<div class="abs step-num" style="left:663px;top:880px">02</div>
<div class="abs step-num" style="left:1017px;top:880px">03</div>
<svg class="abs" style="left:362px;top:950px" width="114" height="18"><path d="M0 9H110" stroke="#1d2a5a" stroke-dasharray="4 3"/><path d="M53 2l9 7-9 7z" fill="#1d2a5a"/></svg>
<svg class="abs" style="left:723px;top:950px" width="114" height="18"><path d="M0 9H110" stroke="#1d2a5a" stroke-dasharray="4 3"/><path d="M53 2l9 7-9 7z" fill="#1d2a5a"/></svg>
<div class="abs step-title" style="left:97px">FINIBUS BONORUM</div>
<div class="abs step-title" style="left:450px">FINIBUS BONORUM</div>
<div class="abs step-title" style="left:810px">FINIBUS BONORUM</div>
<p class="abs step-text" style="left:97px">At vero eos et accusamus et<br>iusto odio dignissimos ducimus<br>qui blanditiis</p>
<p class="abs step-text" style="left:450px">At vero eos et accusamus et<br>iusto odio dignissimos ducimus<br>qui blanditiis</p>
<p class="abs step-text" style="left:810px">At vero eos et accusamus et<br>iusto odio dignissimos ducimus<br>qui blanditiis</p>

<div class="abs photo-training" role="img" aria-label="Photo of an instructor teaching infant CPR on training manikins"></div>
<svg class="abs" style="left:0;top:1216px" width="600" height="42"><path d="M0 0H600V41Z" fill="#fff"/></svg>
<section class="abs panel-grey" style="top:1217px;left:600px;width:600px;height:500px"></section>
<h2 class="abs section-title" style="top:1312px;left:600px;width:600px">About Us</h2>
<p class="abs copy" style="top:1403px;left:600px;width:600px">Sed ut perspiciatis unde omnis iste natus error sit voluptatem<br>accusantium doloremque laudantium, totam rem aperiam, eaque ipsa<br>quae ab illo inventore veritatis et quasi architecto beatae vitae dicta<br>sunt explicabo. Nemo enim ipsam voluptatem quia voluptas sit<br>aspernatur aut odit aut fugit, sed quia consequuntur magni dolores</p>

<section class="abs panel-grey" style="top:1717px;left:0;width:600px;height:490px"></section>
<h2 class="abs section-title" style="top:1817px;left:0;width:600px">Services</h2>
<p class="abs copy" style="top:1904px;left:0;width:600px">Sed ut perspiciatis unde omnis iste natus error sit voluptatem<br>accusantium doloremque laudantium, totam rem aperiam, eaque ipsa<br>quae ab illo inventore veritatis et quasi architecto beatae vitae dicta<br>sunt explicabo. Nemo enim ipsam voluptatem quia voluptas sit<br>aspernatur aut odit aut fugit, sed quia consequuntur magni dolores</p>
<div class="abs photo-sign" role="img" aria-label="Photo of a wall-mounted automatic external defibrillator sign"></div>

<div class="abs map-area" role="img" aria-label="Dark styled map of the New York metro area showing participating regions"></div>
<svg class="abs" style="left:0;top:2185px" width="1200" height="40"><path d="M0 0H1200V32L600 4 0 32Z" fill="#e6e6e6"/></svg>
<svg class="abs" style="left:259px;top:2266px" width="32" height="44" viewBox="0 0 32 44"><path d="M16 44C5 28 0 22 0 15a16 16 0 0 1 32 0c0 7-5 13-16 29z" fill="#6f95d6"/><circle cx="16" cy="15" r="6" fill="#2b2b2b"/></svg>
<svg class="abs" style="left:869px;top:2442px" width="32" height="44" viewBox="0 0 32 44"><path d="M16 44C5 28 0 22 0 15a16 16 0 0 1 32 0c0 7-5 13-16 29z" fill="#6f95d6"/><circle cx="16" cy="15" r="6" fill="#2b2b2b"/></svg>
<svg class="abs" style="left:0;top:2575px" width="30" height="66"><rect width="30" height="66" fill="#fff"/><path d="M8 15h14M15 8v14M8 51h14" stroke="#555" stroke-width="2.5"/><path d="M4 33h22" stroke="#ddd"/></svg>

<h2 class="abs section-title" style="top:2742px;left:0;width:1200px">Testimonials</h2>
<p class="abs quote">“Lorem ipsum dolor sit amet, consectetur adipiscing elit, sed do eiusmod tempor incididunt ut labore et dolore magna aliqua. Ut enim ad minim veniam ”</p>
<p class="abs posted">POSTED ON MAY 30, 2019 / &nbsp;@sitename.com</p>
<span class="abs dot" style="left:575px"></span>
<span class="abs dot" style="left:594px;background:var(--navy)"></span>
<span class="abs dot" style="left:614px"></span>

<footer>
  <div class="abs footer-top">
    <div class="footer-col" style="left:0;width:448px">
      <h3>ABOUT THE PRODUCT</h3>
      <p>Sed ut perspiciatis unde omnis iste natus error sit<br>voluptatem accusantium doloremque laudantium,<br>totam rem aperiam,</p>
    </div>
    <div class="divider" style="left:448px"></div>
    <div class="footer-col" style="left:448px;width:305px">
      <h3>FOLLOW US OUT THERE</h3>
      <div class="social"><span></span><span></span><span></span><span></span></div>
    </div>
    <div class="divider" style="left:753px"></div>
    <div class="footer-col" style="left:753px;width:447px">
      <h3>NEWSLETTER</h3>
    </div>
  </div>
  <div class="email-field">Enter Email id</div>
  <div class="btn-submit">SUBMIT</div>
  <div class="abs" style="top:3272px;left:0;width:1200px;height:1px;background:#8791b0;z-index:1"></div>
  <div class="abs footer-bottom">
    <nav class="footer-nav">
      <svg width="14" height="13" viewBox="0 0 14 13"><path d="M7 0L0 6h2v7h4V9h2v4h4V6h2z" fill="#fff"/></svg>
      <span>ABOUT US</span><span>HOW IT WORKS</span><span>SERVICES</span><span>BLOG</span><span>CONTACT US</span>
    </nav>
    <p class="copyright">© 2019 &nbsp;|&nbsp; www.companyname.com</p>
  </div>
</footer>

</body>
</html>
```